Letterhead for Conveyancing Company

Use existing logo to create a letterhead for a conveyancing company. Must be able to be used in Microsoft Word. Easy to read and professional.
Contact information to be at the bottom.
Bright Oak Conveyancing Pty Ltd
ACN 621 984 736PO Box 535 Campbelltown SA 5074
Mobile - 0461739286
Web address - www.brightoakconveyancing.com.au

Requirements
Must have
• Logo and contact details.
• Simple and professional.

```html
<!DOCTYPE html>
<html lang="en">
<head>
<meta charset="utf-8">
<title>Bright Oak Conveyancing – Letterhead</title>
<link href="https://fonts.googleapis.com/css2?family=Arimo:wght@400;700&family=Tinos&display=swap" rel="stylesheet">
<style>
  :root{
    --backdrop:#dfe1e2;
    --paper:#ffffff;
    --pink:#e0338f;
    --pink-soft:#ef7fbd;
    --grey:#8a8a8c;
    --grey-dark:#6d6d70;
    --text:#707073;
    --rule:#c9c9cb;
  }
  *{box-sizing:border-box;margin:0;padding:0}
  html,body{width:1200px;height:784px;overflow:hidden;background:var(--backdrop)}
  .letterhead{
    position:absolute;left:338px;top:22px;width:524px;height:740px;
    background:var(--paper);box-shadow:0 6px 18px rgba(0,0,0,.18);
    font-family:"Arimo",Arial,sans-serif;color:var(--text);overflow:hidden;
  }
  .header-accent{position:absolute;left:0;top:42px;width:38px;height:6px;background:var(--pink)}
  .brand-name{
    position:absolute;left:50px;top:34px;white-space:nowrap;
    font-family:"Arimo",Arial,sans-serif;font-weight:700;font-size:18px;line-height:22px;
    color:var(--grey-dark);text-transform:uppercase;letter-spacing:.5px;
  }
  .header-rule{
    position:absolute;left:326px;right:0;top:52px;height:6px;background:var(--grey);
    box-shadow:0 3px 3px rgba(0,0,0,.15);
  }
  .letter-body{position:absolute;left:50px;right:56px;top:110px;font-size:9.2px;line-height:13px}
  .letter-body p{margin-bottom:13px}
  .signature{
    position:absolute;left:52px;top:508px;width:150px;height:44px;
    background:linear-gradient(90deg,#f2f2f3,#e6e6e8);border-radius:3px;
  }
  .footer-rule{position:absolute;left:0;right:0;top:600px;height:3px;background:var(--rule)}
  .company-line{
    position:absolute;left:0;right:0;top:613px;text-align:center;
    font-family:"Tinos","Times New Roman",serif;font-size:14px;letter-spacing:.6px;
    color:var(--pink);text-transform:uppercase;
  }
  .contact-line{
    position:absolute;left:16px;right:16px;top:641px;
    display:flex;justify-content:space-between;align-items:center;font-size:7.6px;color:var(--grey-dark);
  }
  .contact-item{display:flex;align-items:center;gap:4px;white-space:nowrap}
  .contact-item svg{width:9px;height:9px;flex:none}
  .footer-band{position:absolute;left:0;right:0;top:664px;height:5px;background:var(--rule)}
  .web-band{
    position:absolute;left:0;right:0;bottom:0;height:42px;
    background:linear-gradient(90deg,var(--pink) 0%,var(--pink) 70%,var(--pink-soft) 100%);
  }
  .web-address{
    position:absolute;right:18px;bottom:14px;font-size:10px;font-weight:700;color:#fff;letter-spacing:.3px;
  }
</style>
</head>
<body>
<main class="letterhead">
  <div class="header-accent"></div>
  <div class="brand-name">Bright Oak Conveyancing</div>
  <div class="header-rule"></div>

  <section class="letter-body">
    <p>Lorem Ipsum is simply dummy text of the printing and typesetting industry. Lorem Ipsum has been the industry's standard dummy text ever since the 1500s, when an unknown printer took a galley of type and scrambled it to make a type specimen book. It has survived not only five centuries, but also the leap into electronic typesetting, remaining essentially unchanged. It was popularised in the 1960s with the release of Typeplate sheets containing Lorem Ipsum passages, and more recently with desktop publishing software like Quillset Publisher including versions of Lorem Ipsum.</p>
    <p>It is a long established fact that a reader will be distracted by the readable content of a page when looking at its layout. The point of using Lorem Ipsum is that it has a more-or-less normal distribution of letters, as opposed to using 'Content here, content here', making it look like readable English. Many desktop publishing packages and web page editors now use Lorem Ipsum as their default model text, and a search for 'lorem ipsum' will uncover many web sites still in their infancy. Various versions have evolved over the years, sometimes by accident, sometimes on purpose (injected humour and the like).</p>
    <p>Contrary to popular belief, Lorem Ipsum is not simply random text. It has roots in a piece of classical Latin literature from 45 BC, making it over 2000 years old. Edwin Harrowgate, a Latin professor at Westbrook Hollis College in Norland, looked up one of the more obscure Latin words, consectetur, from a Lorem Ipsum passage, and going through the cites of the word in classical literature, discovered the undoubtable source. Lorem Ipsum comes from sections 1.10.32 and 1.10.33 of an old Latin treatise, structures used to generate Lorem Ipsum which looks reasonable. The generated Lorem Ipsum is therefore always free from repetition, injected humour, or non-characteristic words etc.</p>
  </section>

  <div class="signature" role="img" aria-label="Handwritten signature"></div>

  <div class="footer-rule"></div>
  <div class="company-line">Bright Oak Conveyancing Pty Ltd</div>
  <div class="contact-line">
    <span class="contact-item"><svg viewBox="0 0 10 10"><circle cx="5" cy="5" r="5" fill="#e0338f"/><path d="M5 2.2a1.9 1.9 0 0 0-1.9 1.9C3.1 5.6 5 7.8 5 7.8s1.9-2.2 1.9-3.7A1.9 1.9 0 0 0 5 2.2z" fill="#fff"/></svg>PO Box 871 Marlowdale SA 5096</span>
    <span class="contact-item"><svg viewBox="0 0 10 10"><circle cx="5" cy="5" r="5" fill="#e0338f"/><path d="M3.3 2.5l1 1-.5.7a4 4 0 0 0 2 2l.7-.5 1 1-.6.8c-2 0-3.9-1.9-3.9-3.9z" fill="#fff"/></svg>0461739286</span>
    <span class="contact-item"><svg viewBox="0 0 10 10"><circle cx="5" cy="5" r="5" fill="#e0338f"/><rect x="2.5" y="3.2" width="5" height="3.6" fill="#fff"/><path d="M2.5 3.2L5 5.3l2.5-2.1" stroke="#e0338f" stroke-width=".6" fill="none"/></svg>contact@brightoakconveyancing.com.au</span>
    <span class="contact-item"><svg viewBox="0 0 10 10"><circle cx="5" cy="5" r="5" fill="#e0338f"/><circle cx="5" cy="5" r="1.6" fill="#fff"/></svg>ACN 583 217 469</span>
  </div>
  <div class="footer-band"></div>
  <div class="web-band"><span class="web-address">www.brightoakconveyancing.com.au</span></div>
</main>
</body>
</html>
```